Kelvor Engineers: Why you should hire us keepsake

New design. Open to plastic cards. We are an engineering firm that designs cell phone towers and commercial buildings. Please check out our website www.kelvorstruct.com for more details. We want people to remember our card and for it to be useful if possible. We want the same look and feel on these cards to be translated to other marketing material we may need such as brochures.

Target Market(s)

Architects, Developers and Telecommunication Carriers

Industry/Entity Type

Engineering

Contact Information for Business Card

Card with our company colors, logo, and innovative design with elements related to our industry.

Font styles to use
Sans Serif

Colors
9bcb3c
abd036
0255a3

Requirements
Must have
• Sleek and hip design
Nice to have
• Bright lime green and navy coloring that pops with an innovative design.
Should not have
• A basic and boring design

```html
<!DOCTYPE html>
<html lang="en">
<head>
<meta charset="utf-8">
<title>Kelvor Engineers – Business Card</title>
<link href="https://fonts.googleapis.com/css2?family=Roboto:wght@400;500;700;900&display=swap" rel="stylesheet">
<style>
  :root {
    --lime: #3ad430;
    --lime-deep: #2fc226;
    --navy: #1b2f5e;
    --navy-text: #1f3467;
    --white: #ffffff;
    --ink-soft: #4a5670;
    --stage: #2b2b2d;
  }
  * { box-sizing: border-box; margin: 0; padding: 0; }
  html, body { width: 1200px; height: 900px; overflow: hidden; }
  body {
    background: var(--stage);
    font-family: "Roboto", Arial, sans-serif;
    position: relative;
  }
  .card {
    position: absolute;
    width: 530px;
    height: 304px;
    border-radius: 24px;
    overflow: hidden;
    box-shadow: 0 18px 40px rgba(0,0,0,.45);
  }

  /* front */
  .card-front { left: 45px; top: 298px; background: var(--white); }
  .card-front .folds { position: absolute; inset: 0; }
  .brand-block { position: absolute; left: 34px; top: 26px; }
  .brand-name {
    font-weight: 900;
    font-size: 62px;
    line-height: 1;
    letter-spacing: -1px;
    color: var(--white);
  }
  .brand-tagline {
    margin-top: 8px;
    font-weight: 500;
    font-size: 13px;
    letter-spacing: 1.2px;
    color: var(--navy-text);
  }
  .contact-block {
    position: absolute;
    right: 34px;
    bottom: 26px;
    text-align: right;
  }
  .person-name { font-weight: 500; font-size: 25px; color: var(--navy-text); }
  .person-role { font-size: 17px; color: var(--lime); margin: 2px 0 12px; }
  .contact-list { list-style: none; }
  .contact-list li {
    display: flex; justify-content: flex-end; align-items: center; gap: 10px;
    font-size: 15px; line-height: 21px; color: var(--ink-soft);
  }
  .contact-list svg { width: 13px; height: 13px; flex: none; }

  /* back */
  .card-back {
    left: 625px; top: 298px;
    background: linear-gradient(160deg, #20376b 0%, var(--navy) 70%);
  }
  .back-brand {
    position: absolute; left: 0; right: 0; top: 100px;
    text-align: center;
    font-weight: 900; font-size: 78px; letter-spacing: -1px;
    color: var(--lime);
  }
  .city-list {
    position: absolute; left: 30px; bottom: 26px;
    font-weight: 500; font-size: 14px; letter-spacing: 1.4px;
    color: var(--white);
  }
  .city-list .sep { color: var(--lime); margin: 0 6px; }
</style>
</head>
<body>

<section class="card card-front" aria-label="Business card front">
  <svg class="folds" viewBox="0 0 530 304" preserveAspectRatio="none" aria-hidden="true">
    <polygon points="0,0 530,0 530,205 0,118" fill="var(--lime)"/>
    <polygon points="0,118 205,152 170,304 0,304" fill="var(--lime-deep)"/>
    <polygon points="0,118 530,205 530,212 0,124" fill="rgba(0,0,0,.06)"/>
  </svg>
  <div class="brand-block">
    <div class="brand-name">Kelvor</div>
    <div class="brand-tagline">MULTI-DISCIPLINE ENGINEERING</div>
  </div>
  <div class="contact-block">
    <div class="person-name">Dana Holloway Reese</div>
    <div class="person-role">Director</div>
    <ul class="contact-list">
      <li>555.014.2290
        <svg viewBox="0 0 16 16"><path d="M3 1l3 3-1.5 2a9 9 0 0 0 5.5 5.5L12 10l3 3-2 2C7 15 1 9 1 3z" fill="var(--lime)"/></svg>
      </li>
      <li>555.017.6634
        <svg viewBox="0 0 16 16"><rect x="4" y="1" width="8" height="14" rx="1.5" fill="none" stroke="var(--lime)" stroke-width="2"/></svg>
      </li>
      <li>dreese@kelvorstruct.com
        <svg viewBox="0 0 16 16"><rect x="1" y="3" width="14" height="10" rx="1" fill="none" stroke="var(--lime)" stroke-width="1.8"/><path d="M1 4l7 5 7-5" fill="none" stroke="var(--lime)" stroke-width="1.8"/></svg>
      </li>
      <li>www.kelvorstruct.com
        <svg viewBox="0 0 16 16"><circle cx="8" cy="8" r="6.5" fill="none" stroke="var(--lime)" stroke-width="1.6"/><path d="M1.5 8h13M8 1.5c3 3 3 10 0 13M8 1.5c-3 3-3 10 0 13" fill="none" stroke="var(--lime)" stroke-width="1.2"/></svg>
      </li>
    </ul>
  </div>
</section>

<section class="card card-back" aria-label="Business card back">
  <div class="back-brand">Kelvor</div>
  <div class="city-list">ATLANTA<span class="sep">/</span>CHARLOTTE<span class="sep">/</span>HOUSTON<span class="sep">/</span>SAN ANTONIO</div>
</section>

</body>
</html>
```